refurbishment of diamond cut alloy wheels

we need to design a flyer that will catch the eye of the customer to refurbish diamond cut alloy wheels. we refurbish the wheels by using the latest CNC machine to precision cut and resurface the wheel. we would like before and after pictures of maybe Valtoren, KRT, Pelo wheels to give it a prestige look. The final design should communicate an expensive look and providing a good image for the business. The colours that I would like to use is black and red which should make the flyer stand out. The logo must sit on a black background without the wordings of specialists in GX, Pelo etc and also without servicing, diagnostics etc as well. This flyer is just to communicate refurbishment of alloy wheels to high standard.

Target Market(s)

any members of the public and car dealerships

Industry/Entity Type

Automotive

Colors

Requirements
Must have
• Wow factor with great images of wheels
Nice to have
• Maybe on the front of the flyer it has a picture of a wheel and then on the back of the flyer it has before and after pictures to show how just how incredible it is to refurbish wheels
Should not have
• other makes of wheels apart from KRT, Pelo, and any other high end makes of vehicles wheels

```html
<!DOCTYPE html>
<html lang="en">
<head>
<meta charset="utf-8">
<title>Apex Wheelworks – Alloy Wheel Refurbishment Flyer</title>
<link rel="stylesheet" href="https://fonts.googleapis.com/css2?family=Didact+Gothic&family=Exo+2:wght@600;700&family=Open+Sans:wght@400;700&display=swap">
<style>
  :root {
    --backdrop: #aeb1b4;
    --ink: #0b0b0c;
    --red: #d4141c;
    --red-bright: #e52a30;
    --red-deep: #8e0a10;
    --white: #ffffff;
    --silver: #c9ccd0;
    --grey-text: #9a9da2;
    --copy-grey: #c9cbce;
  }
  * { box-sizing: border-box; margin: 0; padding: 0; }
  html, body { width: 1200px; height: 3261px; overflow: hidden; }
  body { background: var(--backdrop); position: relative; font-family: "Didact Gothic", sans-serif; color: var(--white); }

  .page { position: absolute; left: 46px; width: 1110px; background: var(--ink); overflow: hidden; box-shadow: 0 6px 18px rgba(0,0,0,.35); }
  .page--front { top: 46px; height: 1558px; }
  .page--back { top: 1653px; height: 1574px; }

  /* brand block */
  .brand { position: absolute; display: flex; align-items: center; justify-content: center; gap: 18px;
           background: linear-gradient(#202024, #0e0e10); }
  .brand__mark { width: 34px; height: 34px; background: var(--red); flex: none; }
  .brand__name { font-family: "Exo 2", sans-serif; font-weight: 700; color: var(--white); letter-spacing: 1px; text-transform: uppercase; line-height: 1.05; }
  .page--front .brand { left: 240px; top: 0; width: 594px; height: 280px; }
  .page--front .brand__name { font-size: 56px; }
  .page--front .brand__mark { width: 42px; height: 42px; }

  /* front hero */
  .hero-wheel { position: absolute; left: 0; top: 280px; width: 1110px; height: 800px;
    background:
      radial-gradient(circle at 36% 52%, rgba(20,20,22,.95) 0 4%, transparent 5%),
      radial-gradient(circle at 36% 52%, #8a8d92 0%, #5c5f64 12%, #2c2e31 26%, #6f7277 38%, #3a3c40 46%, #141516 58%, #0b0b0c 78%),
      linear-gradient(180deg, #1a1b1d, #0b0b0c); }
  .hero-panel { position: absolute; left: 560px; top: 330px; width: 550px; height: 700px; }
  .hero-panel__text { position: absolute; left: 680px; top: 470px; width: 420px; text-align: center;
                      font-size: 47px; line-height: 68px; color: var(--white); }

  .headline { position: absolute; left: 0; width: 1110px; text-align: center; font-family: "Exo 2", sans-serif; font-weight: 700; text-transform: uppercase; letter-spacing: 2px; line-height: 1.2; }
  .headline--top { top: 1110px; font-size: 66px; color: var(--white); }
  .headline--bottom { top: 1202px; font-size: 66px; background: linear-gradient(#ffffff, #8c8f94); -webkit-background-clip: text; background-clip: text; color: transparent; }
  .rule { position: absolute; height: 3px; background: linear-gradient(90deg, transparent, var(--silver), transparent); }
  .page--front .rule { left: 120px; width: 870px; top: 1300px; }

  .enquiry { position: absolute; left: 90px; top: 1380px; width: 440px; font-size: 25px; line-height: 1.35; color: var(--grey-text); }

  .phone-btn { position: absolute; display: flex; align-items: center; gap: 16px; justify-content: center;
               background: linear-gradient(var(--red-bright), var(--red-deep)); border: 3px solid #c7c9cc; border-radius: 14px;
               font-family: "Open Sans", sans-serif; font-size: 44px; color: var(--white); }
  .phone-btn svg { width: 40px; height: 40px; fill: var(--white); }
  .page--front .phone-btn { left: 593px; top: 1366px; width: 437px; height: 97px; }

  /* back */
  .page--back .brand { left: 45px; top: 16px; width: 365px; height: 261px; }
  .page--back .brand__name { font-size: 36px; }
  .back-title { position: absolute; left: 476px; top: 88px; font-size: 46px; line-height: 58px; color: var(--white); }
  .page--back .rule { left: 476px; width: 610px; top: 287px; height: 2px; background: var(--silver); }

  .photo { position: absolute; top: 391px; height: 521px; }
  .photo--before { left: 0; width: 540px;
    background:
      radial-gradient(ellipse at 72% 40%, #d2cbbd 0%, #a39580 18%, #6e6150 36%, #8f8474 48%, #433a31 64%, #1a1714 88%),
      #1a1714;
    border-radius: 0 270px 270px 0 / 0 260px 260px 0; }
  .photo--after { left: 548px; width: 562px;
    background:
      radial-gradient(ellipse at 30% 42%, #f2f3f5 0%, #c3c6cb 18%, #7d8187 34%, #b4b8bd 46%, #4a4d52 64%, #16171a 90%),
      #16171a;
    border-radius: 270px 0 0 270px / 260px 0 0 260px; }
  .tag { position: absolute; background: linear-gradient(var(--red-bright), var(--red-deep)); color: var(--white);
         font-family: "Open Sans", sans-serif; font-size: 32px; text-align: center; }
  .tag--before { left: 78px; top: 358px; width: 225px; height: 56px; line-height: 56px; border-radius: 10px 10px 0 0; }
  .tag--after { left: 738px; top: 867px; width: 254px; height: 62px; line-height: 62px; border-radius: 0 0 10px 10px; }

  .areas { position: absolute; left: 105px; top: 1000px; width: 900px; text-align: center; font-family: "Open Sans", sans-serif; font-weight: 700; font-size: 25px; line-height: 1.4; }
  .copy { position: absolute; left: 110px; width: 890px; text-align: center; font-family: "Open Sans", sans-serif; font-size: 16px; line-height: 1.45; color: var(--copy-grey); }
  .copy--one { top: 1200px; }
  .copy--two { top: 1318px; }

  .cta-bar { position: absolute; left: 0; top: 1462px; width: 1110px; height: 112px; }
  .cta-bar__text { position: absolute; left: 60px; top: 1478px; font-family: "Open Sans", sans-serif; color: var(--white); text-transform: uppercase; }
  .cta-bar__small { font-size: 20px; letter-spacing: 1px; }
  .cta-bar__large { font-size: 40px; letter-spacing: 1px; line-height: 1.2; }
  .page--back .phone-btn { left: 590px; top: 1466px; width: 430px; height: 92px; }
</style>
</head>
<body>

<section class="page page--front">
  <div class="brand"><span class="brand__mark"></span><span class="brand__name">Apex<br>Wheelworks</span></div>

  <div class="hero-wheel" role="img" aria-label="Close-up photo of a dark gunmetal multi-spoke diamond cut alloy wheel"></div>

  <svg class="hero-panel" viewBox="0 0 550 700" aria-hidden="true">
    <defs>
      <linearGradient id="panelRed" x1="0" y1="0" x2="1" y2="1">
        <stop offset="0" stop-color="#e0252c"/>
        <stop offset="1" stop-color="#6e070c"/>
      </linearGradient>
    </defs>
    <path d="M550 0 H150 C5 70 5 630 150 700 H550 Z" fill="#d6d8db"/>
    <path d="M550 14 H162 C30 80 30 620 162 686 H550 Z" fill="url(#panelRed)"/>
  </svg>
  <p class="hero-panel__text">We refurbish the wheels by using the latest CNC machine to precision cut and resurface the wheel.</p>

  <h1 class="headline headline--top">Alloy Wheel</h1>
  <h2 class="headline headline--bottom">Refurbishment Specialists</h2>
  <div class="rule"></div>

  <p class="enquiry">If you need premier Alloy Wheel Refurbishment services in Slough, please contact us:</p>
  <div class="phone-btn">
    <svg viewBox="0 0 24 24" aria-hidden="true"><path d="M6.6 10.8a15.1 15.1 0 0 0 6.6 6.6l2.2-2.2a1 1 0 0 1 1-.25 11.4 11.4 0 0 0 3.6.57 1 1 0 0 1 1 1V20a1 1 0 0 1-1 1A17 17 0 0 1 3 4a1 1 0 0 1 1-1h3.5a1 1 0 0 1 1 1c0 1.25.2 2.45.57 3.57a1 1 0 0 1-.25 1z"/></svg>
    <span>01632 960 418</span>
  </div>
</section>

<section class="page page--back">
  <div class="brand"><span class="brand__mark"></span><span class="brand__name">Apex<br>Wheelworks</span></div>
  <p class="back-title">Alloy wheel<br>Refurbishment Specialists<br>in and around Slough</p>
  <div class="rule"></div>

  <div class="photo photo--before" role="img" aria-label="Before photo: corroded, scuffed silver alloy wheel spokes"></div>
  <div class="photo photo--after" role="img" aria-label="After photo: refurbished diamond cut alloy wheel with bright polished spokes"></div>
  <span class="tag tag--before">Before</span>
  <span class="tag tag--after">After</span>

  <p class="areas">We cater to all locations in and around Colnbrook, Windsor, Hayes, Hounslow, Staines, Ascot and Ashford. For all car body modifications and restorations get in touch with our team of experts today!</p>
  <p class="copy copy--one">If you are looking to refresh the look of your car but don't want the expense of new alloys, with a wide range of limited edition colours to choose from why not consider customising and refurbishing your existing alloys!</p>
  <p class="copy copy--two">If you've had your alloy wheels long enough for them to require alloy refurbishment you can choose from a wide range of colours for refurbishment or choose a brand new set from our comprehensive range. At Prime Rim &amp; Tyre, we stock an extensive range of the latest designs from all the leading suppliers and manufacturers so you are sure to find a stylish new design.</p>

  <svg class="cta-bar" viewBox="0 0 1110 112" aria-hidden="true">
    <defs>
      <linearGradient id="barRed" x1="0" y1="0" x2="0" y2="1">
        <stop offset="0" stop-color="#d81c23"/>
        <stop offset="1" stop-color="#7a080d"/>
      </linearGradient>
    </defs>
    <rect x="0" y="0" width="1110" height="112" fill="#141416"/>
    <path d="M0 0 H580 L530 112 H0 Z" fill="url(#barRed)"/>
  </svg>
  <div class="cta-bar__text">
    <div class="cta-bar__small">If your alloys need refurbishment</div>
    <div class="cta-bar__large">Contact us today</div>
  </div>
  <div class="phone-btn">
    <svg viewBox="0 0 24 24" aria-hidden="true"><path d="M6.6 10.8a15.1 15.1 0 0 0 6.6 6.6l2.2-2.2a1 1 0 0 1 1-.25 11.4 11.4 0 0 0 3.6.57 1 1 0 0 1 1 1V20a1 1 0 0 1-1 1A17 17 0 0 1 3 4a1 1 0 0 1 1-1h3.5a1 1 0 0 1 1 1c0 1.25.2 2.45.57 3.57a1 1 0 0 1-.25 1z"/></svg>
    <span>01632 960 418</span>
  </div>
</section>

</body>
</html>
```